Web Design Project - Old Dellmoor (Bar)

We need a website for a new wine bar/hotel opening in Sydney's Kings Cross area. The concept is a rustic Australiana bar. We intend to use raw materials (sandstone, rusty metal etc) and lots of greenery/plants. It is set to be stylish and accessible to a young and middle age clientele.

The idea is to bring the outside inside.

The venue can cater for 450 people and is in one of the major nightclub strips in Australia. The demographic differs from celebrities to backpackers.
Updates

Target Market(s)

We are targeting 23yr - 40yr olds.

Industry/Entity Type

Hotel

Requirements
Must have
• What I want is a design to reflect is the fit out of the bar. We would like to see a rustic design to reflect the theme of the bar. The theme behind the fit out will be "bringing the outside inside" with lots of plants, wet walls etc.. There will be exposed brickwork, sandstone, timber and rusted steel with laser cut designs throughout the venue.
Nice to have
• I've attached some 3D designs that the venue will be roughly based on.

```html
<!DOCTYPE html>
<html lang="en">
<head>
<meta charset="utf-8">
<title>Old Dellmoor – Reservations</title>
<link rel="stylesheet" href="https://fonts.googleapis.com/css2?family=Noticia+Text:wght@400;700&family=Open+Sans:wght@400;700&display=swap">
<style>
:root{
  --wood-dark:#2a1a10;
  --wood-mid:#4a3424;
  --header-light:#8c6a4c;
  --header-dark:#5e4430;
  --bar:#361408;
  --sand:#dbbb8a;
  --cream:#f3ddb6;
  --maroon:#6b0e0e;
  --red:#b80d0d;
  --nav-text:#e8c99a;
  --ink:#2b1a10;
  --body:#3a2a1e;
  --field-label:#c9a98a;
  --dir-btn:#d9b886;
}
*{margin:0;padding:0;box-sizing:border-box}
html,body{width:800px;height:1200px;overflow:hidden}
body{background:var(--sand);font-family:"Open Sans",sans-serif;color:var(--body);position:relative}
.wood-strip{position:absolute;left:0;width:800px;background:repeating-linear-gradient(90deg,var(--wood-dark) 0 78px,var(--wood-mid) 78px 80px,#3a2616 80px 160px)}
.wood-top{top:0;height:61px;border-bottom:8px solid var(--bar)}
.wood-bottom{top:1180px;height:20px}
.masthead{position:absolute;top:61px;left:0;width:800px;height:172px;background:radial-gradient(ellipse at center,var(--header-light),var(--header-dark) 85%);display:flex;flex-direction:column;align-items:center;justify-content:center}
.brand-name{font-family:"Noticia Text",serif;font-size:30px;font-weight:400;color:#1a120c;letter-spacing:2px;margin-top:40px}
.main-nav{position:absolute;top:233px;left:0;width:800px;height:47px;background:var(--bar);border-top:1px dashed #9a7a5a;border-bottom:1px dashed #9a7a5a;display:flex;align-items:center}
.main-nav a{flex:1;text-align:center;color:var(--nav-text);text-decoration:none;font-weight:700;font-size:14px}
.main-nav a.active{color:#fff2dc}
.page-title{position:absolute;top:308px;left:29px;font-family:"Noticia Text",serif;font-weight:700;font-size:44px;color:var(--maroon)}
.page-sub{position:absolute;top:366px;left:29px;font-family:"Noticia Text",serif;font-size:17px;color:var(--ink)}
.photo{position:absolute;top:400px;width:231px;height:178px;border:2px solid var(--cream);border-radius:3px}
.photo-1{left:29px;background:linear-gradient(160deg,#3a3a28,#8a4a30 55%,#c9b8a8)}
.photo-2{left:283px;background:linear-gradient(170deg,#4a3020,#7a5038 50%,#b8a898)}
.photo-3{left:539px;background:linear-gradient(120deg,#e8c070,#5a2410 45%,#1a0a04)}
.intro{position:absolute;top:597px;left:31px;font-size:11.5px;line-height:15px}
.divider{position:absolute;top:646px;left:0;width:800px;height:3px;background:#c49e6c}
.booking-form{position:absolute;top:673px;left:29px;width:486px}
.field{height:29px;background:var(--bar);border-radius:4px;margin-bottom:4.5px;font-family:"Noticia Text",serif;font-weight:700;font-size:15px;color:var(--field-label);padding:3px 5px}
.field.message{height:106px}
.send{position:absolute;right:0;top:213px;background:var(--red);color:#fff;font-family:"Noticia Text",serif;font-weight:700;font-size:15px;padding:3px 5px;border-radius:3px}
.online{position:absolute;top:668px;left:539px;width:232px}
.online h2{font-family:"Noticia Text",serif;font-weight:700;font-size:25px;color:var(--red);white-space:nowrap}
.online p{font-size:11.5px;line-height:15.5px;margin-top:8px}
.call-box{position:absolute;top:799px;left:539px;width:232px;height:86px;background:var(--cream);border-radius:3px;text-align:center;font-family:"Noticia Text",serif}
.call-box .label{color:var(--red);font-size:15px;margin-top:18px}
.call-box .phone{font-weight:700;font-size:24px;color:var(--ink);margin-top:2px}
.info-band{position:absolute;top:931px;left:0;width:800px;height:200px;background:var(--bar);border-top:1px dashed #9a7a5a;border-bottom:1px dashed #9a7a5a}
.info-card{position:absolute;top:32px;width:231px;height:107px;background:var(--cream);border-radius:2px;text-align:center;padding-top:24px}
.info-card h3{font-family:"Noticia Text",serif;font-weight:700;font-size:22px;color:var(--ink);line-height:24px}
.info-card p{font-size:11.5px;line-height:15.5px;margin-top:3px}
.card-where{left:29px}.card-hours{left:283px}.card-chef{left:539px;padding-top:18px}
.dir-btn{display:block;margin:6px 17px 0;background:var(--dir-btn);color:var(--red);font-family:"Noticia Text",serif;font-weight:700;font-size:14.5px;padding:5px 0;border-radius:3px}
.hours{font-family:"Noticia Text",serif;font-weight:700;font-size:17px;color:var(--red);margin-top:10px}
.site-footer{position:absolute;top:1131px;left:0;width:800px;height:49px;background:linear-gradient(90deg,#5a3a1e,#9a7040 50%,#5a3a1e);display:flex;align-items:center;justify-content:space-between;padding:0 24px 0 25px;color:#fff;font-size:12px}
.social{display:flex;gap:9px}
.social span{width:12px;height:12px;background:#fff;border-radius:50%}
</style>
</head>
<body>
<div class="wood-strip wood-top"></div>
<header class="masthead">
  <div class="brand-name">OLD DELLMOOR</div>
</header>
<nav class="main-nav">
  <a href="#">HOME</a><a href="#">ABOUT US</a><a href="#">MENU</a><a href="#" class="active">RESERVATIONS</a><a href="#">LOCATION</a>
</nav>
<h1 class="page-title">Reservations</h1>
<p class="page-sub">Book a Table. We'd love to have you in the Old Dellmoor!</p>
<div class="photo photo-1" role="img" aria-label="Bar interior with brick walls, plants and high tables"></div>
<div class="photo photo-2" role="img" aria-label="Long bar room with timber ceiling and hanging greenery"></div>
<div class="photo photo-3" role="img" aria-label="Red wine bottles and a glass on the bar"></div>
<p class="intro">I'm a Paragraph. Click here to add your own text and edit me. It's easy.<br>Just click “Edit Text” or double click me and you can start adding your own content...</p>
<div class="divider"></div>
<form class="booking-form">
  <div class="field">Name</div>
  <div class="field">Email</div>
  <div class="field">Subject</div>
  <div class="field message"></div>
  <div class="send">Send</div>
</form>
<section class="online">
  <h2>Online reservations</h2>
  <p>I'm a Paragraph. Click here to add your own text and edit me. It's easy. Just click “Edit Text” or double click me and you can start adding your own content and make changes to the font.</p>
</section>
<div class="call-box"><div class="label">CALL US NOW</div><div class="phone">1-800-000-0000</div></div>
<section class="info-band">
  <div class="info-card card-where"><h3>WHERE ARE WE?</h3><p>48 Laneway Rd. Sydney, AU 20110</p><span class="dir-btn">GET DIRECTIONS NOW</span></div>
  <div class="info-card card-hours"><h3>OPENING HOURS</h3><p>We're open everyday</p><div class="hours">12:00pm-1:00am</div></div>
  <div class="info-card card-chef"><h3>CHEF AT HOME</h3><p>I'm a Paragraph. Click here to add<br>your own text and edit me. It's easy.<br>Just click “Edit Text”</p></div>
</section>
<footer class="site-footer"><span>© 2013 by Old Dellmoor.</span><div class="social"><span></span><span></span><span></span></div></footer>
<div class="wood-strip wood-bottom"></div>
</body>
</html>
```